Stationery Design Project

I need a design that is simple, clean and modern, in square style, bold font.
The majority of the design needs to be White and Black with a splash of Red colour.
I would like a design for business cards and letter heads with the following information.
Name, Title, Phone, Fax, Email, Website and company ABN number

Target Market(s)

25 to 65 years old real estate clients

Industry/Entity Type

Business

Requirements
Must have
• All designs must incorporate Company Logo, Name, Title, Phone, Fax, Email, Website and company ABN number

```html
<!DOCTYPE html>
<html lang="en">
<head>
<meta charset="utf-8">
<title>Ravenmoor Real Estate – Business Card</title>
<link rel="stylesheet" href="https://fonts.googleapis.com/css2?family=Lato:wght@400;700&display=swap">
<style>
  :root {
    --bg: #dfe3e6;
    --paper: #ffffff;
    --ink: #231f20;
    --ink-soft: #3a3a3a;
    --card-dark: #2b2929;
    --red: #e0252b;
    --white: #ffffff;
  }
  * { margin: 0; padding: 0; box-sizing: border-box; }
  html, body {
    width: 1200px; height: 960px; overflow: hidden;
    background: var(--bg);
    font-family: "Lato", sans-serif;
  }
  .stage {
    width: 1200px; height: 960px;
    display: flex; flex-direction: column;
    align-items: center; justify-content: center; gap: 60px;
  }
  .card {
    width: 560px; height: 320px;
    position: relative; overflow: hidden;
    box-shadow: 0 6px 18px rgba(0,0,0,.18);
  }
  /* Front */
  .card--front { background: var(--paper); }
  .card--front .base-band {
    position: absolute; left: 0; right: 0; bottom: 0; height: 24px;
    background: var(--ink);
  }
  .brand-block {
    position: absolute; left: 40px; top: 0; bottom: 24px; width: 220px;
    display: flex; align-items: center; gap: 12px;
  }
  .brand-mark { width: 16px; height: 16px; background: var(--red); flex: none; }
  .brand-name {
    font-weight: 700; font-size: 30px; letter-spacing: 1px;
    color: var(--ink); text-transform: uppercase;
  }
  .details {
    position: absolute; left: 300px; top: 52px; color: var(--ink-soft);
  }
  .person-name { font-size: 23px; font-weight: 400; letter-spacing: .5px; color: var(--ink); }
  .person-title { font-size: 16px; margin-top: 4px; }
  .contact-list { list-style: none; margin-top: 24px; }
  .contact-list li {
    display: flex; align-items: center; gap: 10px;
    font-size: 15px; line-height: 22px;
  }
  .contact-list svg { width: 14px; height: 14px; flex: none; }
  .abn { font-size: 15px; margin-top: 22px; }
  .web--front { font-size: 15px; font-weight: 700; color: var(--red); margin-top: 4px; }
  /* Back */
  .card--back {
    background: var(--card-dark);
    display: flex; flex-direction: column; align-items: center; justify-content: center;
  }
  .back-brand {
    display: flex; flex-direction: column; align-items: center;
    color: var(--white); font-weight: 400; text-transform: uppercase;
  }
  .back-brand .brand-name--back { font-size: 50px; letter-spacing: 3px; color: var(--white); font-weight: 400; }
  .back-brand .brand-sub { font-size: 16px; letter-spacing: 14px; margin-top: 4px; color: var(--white); font-weight: 400; }
  .web--back {
    margin-top: 44px; font-size: 16px; font-weight: 700;
    color: var(--red); letter-spacing: .5px;
  }
</style>
</head>
<body>
<main class="stage">
  <section class="card card--front" aria-label="Business card front">
    <div class="brand-block">
      <span class="brand-mark"></span>
      <span class="brand-name">Ravenmoor</span>
    </div>
    <div class="details">
      <h1 class="person-name">LENA HARTWELL</h1>
      <p class="person-title">Operation Manager</p>
      <ul class="contact-list">
        <li>
          <svg viewBox="0 0 14 14" aria-hidden="true"><rect x="2" y="1" width="10" height="12" rx="1" fill="none" stroke="var(--red)" stroke-width="1.5"/><rect x="4" y="3" width="6" height="3" fill="var(--red)"/><circle cx="5" cy="9" r=".9" fill="var(--red)"/><circle cx="9" cy="9" r=".9" fill="var(--red)"/></svg>
          (221) 33 410 27 58
        </li>
        <li>
          <svg viewBox="0 0 14 14" aria-hidden="true"><rect x="4" y="1" width="6" height="4" fill="var(--red)"/><rect x="1" y="5" width="12" height="5" rx="1" fill="var(--red)"/><rect x="4" y="9" width="6" height="4" fill="var(--paper)" stroke="var(--red)" stroke-width="1.2"/></svg>
          (221) 33 410 27 59
        </li>
        <li>
          <svg viewBox="0 0 14 14" aria-hidden="true"><rect x="1" y="3" width="12" height="8" fill="none" stroke="var(--red)" stroke-width="1.4"/><path d="M1 3 L7 8 L13 3" fill="none" stroke="var(--red)" stroke-width="1.4"/></svg>
          name@ravenmoor-estate.com
        </li>
      </ul>
      <p class="abn">ABN 987654321</p>
      <p class="web--front">www.ravenmoor-estate.com</p>
    </div>
    <div class="base-band"></div>
  </section>

  <section class="card card--back" aria-label="Business card back">
    <div class="back-brand">
      <span class="brand-name--back">Ravenmoor</span>
      <span class="brand-sub">Real Estate</span>
    </div>
    <p class="web--back">www.ravenmoor-estate.com</p>
  </section>
</main>
</body>
</html>
```